Business Card Design for Marketing Firm

Looking for business card design for higher end marketing firm. Clean but impressionable/trendy. We are a marketing firm that represents manufacturers in the foodservice equipment and supply industry. Our customers are end users such has hotels, restaurants, country clubs, convention centers and casinos as well as distributors of restaurants supplies and equipment, and manufacturers of foodservice equipment and supplies.
Target Market(s)
Hotels, Restaurants, Supply & Equipment Distributors, Foodservice Manufacturers
Industry/Entity Type
Foodservice/Hospitality
Contact Information for Business Card
Name, Title, Contact Number, Email, Website, Social Media, Address
Requirements
Must have
- Clean & Simple but Serious and Impressionable

```html
<!DOCTYPE html>
<html lang="en">
<head>
<meta charset="utf-8">
<title>Meridian Hospitality Reps – Business Card</title>
<link href="https://fonts.googleapis.com/css2?family=Open+Sans:wght@400;700&display=swap" rel="stylesheet">
<style>
  :root {
    --brand-navy: #2b2a78;
    --paper-white: #ffffff;
    --canvas-bg: #ecebef;
    --card-shadow: rgba(20, 20, 50, 0.22);
  }
  * { box-sizing: border-box; margin: 0; padding: 0; }
  html, body {
    width: 1200px; height: 834px; overflow: hidden;
    background: var(--canvas-bg);
    font-family: "Open Sans", Arial, sans-serif;
  }
  .canvas { position: relative; width: 1200px; height: 834px; }

  .card {
    position: absolute;
    border-radius: 26px;
    overflow: hidden;
    box-shadow: 0 10px 28px var(--card-shadow);
  }

  /* Front: vertical card */
  .card-front {
    left: 90px; top: 117px; width: 360px; height: 600px;
    background: var(--brand-navy);
  }
  .card-front .swoosh { position: absolute; inset: 0; }
  .contact-block {
    position: absolute; left: 34px; top: 44px;
    color: var(--paper-white);
  }
  .person-name { font-size: 22px; font-weight: 700; letter-spacing: 0.3px; }
  .person-title { font-size: 14px; margin-top: 2px; }
  .address { font-size: 14px; line-height: 1.35; margin-top: 18px; }
  .contact-list { list-style: none; margin-top: 10px; font-size: 14px; line-height: 1.5; }
  .contact-list li { display: flex; align-items: center; gap: 7px; }
  .contact-list svg { width: 12px; height: 12px; flex: none; }

  .wordmark {
    display: flex; align-items: center; gap: 10px;
    font-weight: 700; letter-spacing: 1.5px; line-height: 1.25;
  }
  .wordmark-dot { border-radius: 50%; flex: none; }

  .card-front .wordmark {
    position: absolute; left: 150px; top: 420px;
    color: var(--brand-navy); font-size: 17px;
  }
  .card-front .wordmark-dot { width: 14px; height: 14px; background: var(--brand-navy); }

  /* Back: horizontal card */
  .card-back {
    left: 510px; top: 237px; width: 600px; height: 360px;
    background: var(--brand-navy);
  }
  .card-back .wordmark {
    position: absolute; left: 0; right: 0; top: 130px;
    justify-content: center;
    color: var(--paper-white); font-size: 30px;
  }
  .card-back .wordmark-dot { width: 22px; height: 22px; background: var(--paper-white); }
  .social-row {
    position: absolute; left: 0; right: 0; top: 250px;
    display: flex; justify-content: center; gap: 8px; list-style: none;
  }
  .social-row li {
    width: 20px; height: 20px; border-radius: 50%;
    border: 1.5px solid var(--paper-white);
  }
</style>
</head>
<body>
<main class="canvas">

  <section class="card card-front" aria-label="Business card front">
    <svg class="swoosh" viewBox="0 0 360 600" preserveAspectRatio="none" aria-hidden="true">
      <path d="M360 238 C190 258 110 420 112 600 L360 600 Z" fill="var(--paper-white)"/>
      <path d="M360 226 C175 246 88 420 86 600" fill="none" stroke="var(--paper-white)" stroke-width="2.5"/>
      <path d="M360 218 C165 236 70 420 66 600" fill="none" stroke="var(--paper-white)" stroke-width="1.5"/>
    </svg>

    <div class="contact-block">
      <h1 class="person-name">DANA WHITFIELD</h1>
      <p class="person-title">Managing Director</p>
      <p class="address">48 Harbor Lane, Easton<br>Ohio, 43001</p>
      <ul class="contact-list">
        <li>
          <svg viewBox="0 0 24 24" aria-hidden="true"><path fill="#fff" d="M6.6 10.8a15 15 0 0 0 6.6 6.6l2.2-2.2c.3-.3.7-.4 1-.2 1.1.4 2.3.6 3.6.6.6 0 1 .4 1 1V20c0 .6-.4 1-1 1A17 17 0 0 1 3 4c0-.6.4-1 1-1h3.5c.6 0 1 .4 1 1 0 1.3.2 2.5.6 3.6.1.3 0 .7-.2 1z"/></svg>
          555 014 2280
        </li>
        <li>
          <svg viewBox="0 0 24 24" aria-hidden="true"><rect x="2" y="5" width="20" height="14" rx="2" fill="#fff"/><path d="M3 6l9 7 9-7" fill="none" stroke="var(--brand-navy)" stroke-width="2"/></svg>
          info@meridianreps.com
        </li>
        <li>
          <svg viewBox="0 0 24 24" aria-hidden="true"><circle cx="12" cy="12" r="10" fill="none" stroke="#fff" stroke-width="2.5"/><path d="M2 12h20M12 2c3 3 3 17 0 20M12 2c-3 3-3 17 0 20" fill="none" stroke="#fff" stroke-width="2"/></svg>
          www.meridianreps.com
        </li>
      </ul>
    </div>

    <div class="wordmark">
      <span class="wordmark-dot"></span>
      <span>MERIDIAN<br>HOSPITALITY<br>REPS</span>
    </div>
  </section>

  <section class="card card-back" aria-label="Business card back">
    <div class="wordmark">
      <span class="wordmark-dot"></span>
      <span>MERIDIAN HOSPITALITY REPS</span>
    </div>
    <ul class="social-row" aria-label="Social media links">
      <li></li><li></li><li></li><li></li><li></li>
    </ul>
  </section>

</main>
</body>
</html>
```